KTR Design Business Card

I need to develop a business card for my real estate design and investment company. Something clean, classic and professional with a modern vibe.

Industry/Entity Type

Real Estate

Font styles to use
Serif
Sans Serif

```html
<!DOCTYPE html>
<html lang="en">
<head>
<meta charset="UTF-8">
<title>KTR Design Business Card</title>
<link rel="stylesheet" href="https://fonts.googleapis.com/css2?family=Montserrat:wght@300;400;500&display=swap">
<style>
  :root {
    --backdrop: #d9d9d7;
    --card: #050505;
    --ink-bright: #f2f2f2;
    --ink-muted: #8c8c8c;
    --ink-soft: #b5b5b5;
  }
  * { margin: 0; padding: 0; box-sizing: border-box; }
  html, body {
    width: 1200px;
    height: 1200px;
    overflow: hidden;
    background: var(--backdrop);
    font-family: "Montserrat", sans-serif;
  }
  .sheet {
    width: 1200px;
    height: 1200px;
    display: flex;
    flex-direction: column;
    align-items: center;
    justify-content: center;
    gap: 70px;
  }
  .card {
    position: relative;
    width: 700px;
    height: 400px;
    background: var(--card);
    border-radius: 4px;
    box-shadow: 0 6px 18px rgba(0,0,0,0.18);
  }
  .brand {
    color: var(--ink-bright);
    font-weight: 300;
    letter-spacing: 0.08em;
    white-space: nowrap;
  }
  .card--front .brand {
    position: absolute;
    top: 50%;
    left: 50%;
    transform: translate(-50%, -50%);
    font-size: 44px;
  }
  .card--back .brand {
    position: absolute;
    top: 50px;
    left: 50px;
    font-size: 34px;
  }
  .holder {
    position: absolute;
    left: 50px;
    top: 200px;
  }
  .holder-name {
    color: var(--ink-soft);
    font-size: 26px;
    font-weight: 500;
    letter-spacing: 0.06em;
    text-transform: uppercase;
  }
  .holder-title {
    color: var(--ink-muted);
    font-size: 24px;
    font-weight: 400;
    margin-top: 4px;
  }
  .contact {
    position: absolute;
    right: 50px;
    bottom: 50px;
    list-style: none;
    color: var(--ink-soft);
    font-size: 19px;
    font-weight: 400;
    line-height: 1.35;
    white-space: nowrap;
  }
  .contact-label { display: inline-block; width: 34px; }
</style>
</head>
<body>
  <main class="sheet">
    <section class="card card--front">
      <p class="brand">KTR Design</p>
    </section>
    <section class="card card--back">
      <p class="brand">KTR Design</p>
      <div class="holder">
        <p class="holder-name">Daniel Reyes</p>
        <p class="holder-title">Owner - Title</p>
      </div>
      <ul class="contact">
        <li><span class="contact-label">t.</span>310.555.014</li>
        <li><span class="contact-label">m.</span>310.555.027</li>
        <li>dreyes@ktrdesign.com</li>
      </ul>
    </section>
  </main>
</body>
</html>
```